Design a New Business Card for Our Company

We are looking for fresh, unique, and a modern business card that reflects our roots as digital marketing agency focused on SEM.

Industry/Entity Type

Marketing

Contact Information for Business Card

looking for very unique out of the box designs. clean and modern that compliments our logo

Requirements
Must have
• colors should match our logo
• Front should have name, address, email, and phone/fax of the person, phone/fax are the same number
• back should have our url

```html
<!DOCTYPE html>
<html lang="en">
<head>
<meta charset="utf-8">
<title>Brightpath Media – Business Card</title>
<link rel="stylesheet" href="https://fonts.googleapis.com/css2?family=Open+Sans:wght@400;700&display=swap">
<style>
  :root {
    --backdrop: #ebe8e5;
    --card: #ffffff;
    --brand-blue: #4f8fd0;
    --brand-grey: #a3a3a3;
    --text-grey: #8c8c8c;
    --card-shadow: rgba(0, 0, 0, 0.12);
  }
  * { box-sizing: border-box; margin: 0; padding: 0; }
  html, body {
    width: 1200px;
    height: 997px;
    overflow: hidden;
    background: var(--backdrop);
    font-family: "Open Sans", sans-serif;
  }
  .card {
    position: absolute;
    width: 560px;
    height: 320px;
    background: var(--card);
    box-shadow: 0 10px 28px var(--card-shadow);
    overflow: hidden;
  }
  .card--front { left: 60px; top: 150px; }
  .card--back { left: 580px; top: 520px; }

  .wordmark {
    position: absolute;
    display: flex;
    align-items: center;
    gap: 10px;
    color: var(--brand-blue);
    font-weight: 700;
    letter-spacing: -0.5px;
    white-space: nowrap;
  }
  .wordmark__dot {
    display: block;
    border-radius: 50%;
    background: var(--brand-grey);
  }
  .card--front .wordmark { left: 36px; top: 120px; font-size: 17px; }
  .card--front .wordmark__dot { width: 22px; height: 22px; }

  .card--back .wordmark { left: 40px; top: 128px; font-size: 30px; }
  .back__url {
    position: absolute;
    left: 42px;
    top: 172px;
    color: var(--brand-grey);
    font-size: 12px;
    letter-spacing: 3.5px;
    text-transform: uppercase;
    white-space: nowrap;
  }
  .back__disc {
    position: absolute;
    right: 40px;
    top: 50%;
    width: 200px;
    height: 200px;
    margin-top: -100px;
    border-radius: 50%;
    background: var(--brand-blue);
  }

  .contact {
    position: absolute;
    left: 330px;
    top: 70px;
    color: var(--text-grey);
    font-size: 12.5px;
    line-height: 1.45;
  }
  .contact__name {
    color: var(--brand-blue);
    font-weight: 700;
    font-size: 17px;
    line-height: 1.2;
  }
  .contact__title { margin-bottom: 8px; }
  .contact__address { margin-bottom: 6px; }
  .contact__list { list-style: none; }
  .contact__item { display: flex; align-items: center; gap: 8px; }
  .contact__icon { width: 13px; height: 13px; fill: var(--brand-blue); flex: none; }
</style>
</head>
<body>

<section class="card card--front" aria-label="Business card front">
  <div class="wordmark">
    <span class="wordmark__dot"></span>
    <span class="wordmark__name">brightpath media</span>
  </div>

  <div class="contact">
    <p class="contact__name">Dana Whitfield</p>
    <p class="contact__title">Owner</p>
    <p class="contact__address">N. 4 Harbor Lane, Suite 200,<br>Lakeview, OR 97000</p>
    <ul class="contact__list">
      <li class="contact__item">
        <svg class="contact__icon" viewBox="0 0 16 16" aria-label="Phone"><path d="M3 1h3l1.5 3.5-2 1.3a9 9 0 0 0 4.7 4.7l1.3-2L15 10v3a2 2 0 0 1-2 2A12 12 0 0 1 1 3a2 2 0 0 1 2-2z"/></svg>
        <span>555.210.4870</span>
      </li>
      <li class="contact__item">
        <svg class="contact__icon" viewBox="0 0 16 16" aria-label="Fax"><path d="M4 1h6l2 2v3h1a2 2 0 0 1 2 2v5h-2v2H3v-2H1V8a2 2 0 0 1 2-2h1zm1 1v4h6V3.5L9.5 2zM4.5 11v3h7v-3z"/></svg>
        <span>555.210.4870</span>
      </li>
      <li class="contact__item">
        <svg class="contact__icon" viewBox="0 0 16 16" aria-label="Email"><path d="M1 3h14v10H1zm1.5 1.2v.3L8 8.3l5.5-3.8v-.3zM2.5 6v5.8h11V6L8 9.8z"/></svg>
        <span>info@brightpathmedia.com</span>
      </li>
      <li class="contact__item">
        <svg class="contact__icon" viewBox="0 0 16 16" aria-label="Website"><path d="M8 1a7 7 0 1 0 0 14A7 7 0 0 0 8 1zm0 1.3c.8.9 1.4 2.2 1.6 3.7H6.4C6.6 4.5 7.2 3.2 8 2.3zM2.4 7.3h2.7c0 .5 0 1 .1 1.4H2.4a5.6 5.6 0 0 1 0-1.4zm8.5 0h2.7a5.6 5.6 0 0 1 0 1.4h-2.8zM6.4 10h3.2c-.2 1.5-.8 2.8-1.6 3.7-.8-.9-1.4-2.2-1.6-3.7z"/></svg>
        <span>www.brightpathmedia.com</span>
      </li>
    </ul>
  </div>
</section>

<section class="card card--back" aria-label="Business card back">
  <div class="wordmark">
    <span class="wordmark__name">brightpath media</span>
  </div>
  <p class="back__url">www.brightpathmedia.com</p>
  <span class="back__disc" aria-hidden="true"></span>
</section>

</body>
</html>
```